Business card design for new eCommerce site focusing on integrity and strong businsess tactics

We need a business card that will stand out and be memorable. Something with color that matches our company logo colors. Think high end version of Pactivo. There are 2 logos provided. The parent company is called Amber Ledge Partners and we are presenting a new and very exciting eCommerce site called BrightHarborTrade.example.

Target Market(s)

Our target markets are in the Activities, Food and Beverage, Health and Beauty

Industry/Entity Type

Marketing

Contact Information for Business Card

We have 4 members that need cards...I will provide all info to the winner of the design contest
Business Address is
4870 West 63rd Avenue, Suite C207
Phoenix AZ 85731

Font styles to use
Serif
Sans Serif

Colors

Designer to choose colors to be used in the design.

Requirements
Must have
• The card must be memorable...should be unique in design but must exude integrity and be playful .
• I have provided several colors or our parent company...please feel free to use which ever
Nice to have
• I will leave this up to you. Feel free to use other images of your choosing that wraps around our client.....Activities, Dining, Health, Beauty
Should not have
• just dont be boring

```html
<!DOCTYPE html>
<html lang="en">
<head>
<meta charset="utf-8">
<title>BrightHarborTrade.example — Business Card</title>
<link rel="stylesheet" href="https://fonts.googleapis.com/css2?family=Questrial&family=Fira+Sans+Condensed:wght@400;500&family=Roboto:wght@700&display=swap">
<style>
  :root {
    --backdrop: #ece9e4;
    --card-white: #f6f6f4;
    --brand-blue: #2b7db2;
    --brand-green: #7cc242;
    --ink: #3d3d3d;
    --ink-soft: #5a5a5a;
    --rule: #b9b9b9;
    --white: #ffffff;
  }
  * { box-sizing: border-box; margin: 0; padding: 0; }
  html, body { width: 1200px; height: 960px; overflow: hidden; }
  body { background: var(--backdrop); position: relative; font-family: "Questrial", sans-serif; }

  .card {
    position: absolute;
    width: 600px;
    height: 342px;
    border-radius: 22px;
    box-shadow: 0 3px 8px rgba(0,0,0,0.25);
  }
  .card--front { left: 303px; top: 131px; background: var(--card-white); }
  .card--back  { left: 299px; top: 490px; background: var(--brand-blue); }

  /* Front: brand lockup */
  .brand { position: absolute; left: 92px; top: 98px; display: flex; align-items: center; gap: 12px; }
  .brand__dot { width: 38px; height: 38px; border-radius: 50%; background: var(--brand-green); flex: none; }
  .brand__name { font-size: 27px; color: var(--brand-blue); font-family: "Questrial", sans-serif; letter-spacing: 0.2px; }
  .tagline {
    position: absolute; left: 194px; top: 143px;
    font-size: 15px; letter-spacing: 1.3px; color: var(--ink);
  }

  /* Front: person block */
  .person { position: absolute; right: 318px; top: 203px; text-align: right; }
  .person__name { font-family: "Fira Sans Condensed", sans-serif; font-weight: 500; font-size: 23px; color: var(--brand-blue); line-height: 26px; }
  .person__role { font-family: "Fira Sans Condensed", sans-serif; font-size: 15px; color: var(--brand-green); line-height: 18px; margin-bottom: 3px; }
  .person__address { font-family: "Fira Sans Condensed", sans-serif; font-size: 14.5px; color: var(--ink-soft); line-height: 19px; white-space: nowrap; }

  .divider { position: absolute; left: 298px; top: 207px; width: 1px; height: 78px; background: var(--rule); }

  .contacts { position: absolute; left: 318px; top: 206px; list-style: none; }
  .contacts li { display: flex; align-items: center; height: 19.5px; font-size: 14px; color: var(--ink); }
  .contacts svg { width: 14px; height: 14px; margin-right: 9px; fill: var(--brand-blue); flex: none; }

  /* Back */
  .back-mark {
    position: absolute; left: 262px; top: 72px;
    width: 76px; height: 76px; border-radius: 50%;
    border: 4px solid var(--white);
  }
  .back-name {
    position: absolute; left: 0; right: 0; top: 214px; text-align: center;
    font-family: "Roboto", sans-serif; font-weight: 700; font-size: 36px; color: var(--white);
  }
</style>
</head>
<body>

<section class="card card--front" aria-label="Business card front">
  <div class="brand">
    <span class="brand__dot"></span>
    <span class="brand__name">BrightHarborTrade.example</span>
  </div>
  <p class="tagline">Activities-Dining-Health-Beauty</p>

  <div class="person">
    <p class="person__name">DANA WHITLOW</p>
    <p class="person__role">CEO/FOUNDER</p>
    <p class="person__address">4870 West 63rd Avenue</p>
    <p class="person__address">Suite C207, Phoenix AZ 85731</p>
  </div>

  <div class="divider"></div>

  <ul class="contacts">
    <li>
      <svg viewBox="0 0 16 16" aria-hidden="true"><path d="M3.6 1.2l2.3 2.9-1.3 1.7c.9 2 2.5 3.6 4.5 4.5l1.7-1.3 2.9 2.3-1.4 2.6C6.8 13.6 2.4 9.2 1 3.1z"/></svg>
      555 214 7730
    </li>
    <li>
      <svg viewBox="0 0 16 16" aria-hidden="true"><path d="M4.5 1h7v14h-7zM5.8 2.6v9.6h4.4V2.6zM7.3 13h1.4v1H7.3z" fill-rule="evenodd"/></svg>
      555 309 4418
    </li>
    <li>
      <svg viewBox="0 0 16 16" aria-hidden="true"><path d="M1 3.5h14v9H1zM2.3 4.5L8 8.6l5.7-4.1z"/></svg>
      dana@brightharbortrade.example
    </li>
    <li>
      <svg viewBox="0 0 16 16" aria-hidden="true"><circle cx="8" cy="8" r="7"/><path d="M4 5.5l3 1-1 2.5 2 2-1 3M10 2.5l-1 3 3 1.5" stroke="#f6f6f4" stroke-width="1.2" fill="none"/></svg>
      www.brightharbortrade.example
    </li>
  </ul>
</section>

<section class="card card--back" aria-label="Business card back">
  <span class="back-mark"></span>
  <p class="back-name">Amber Ledge Partners</p>
</section>

</body>
</html>
```